Business Card for Coastal Tundrabridge Advisory

We need a business card for Coastal Tundrabridge Advisory. The company website address is provided below. The company logo is attached. We provide specialized permafrost services to the mining, transportation, and oil & gas industries. The card should be prepared for:
Matthias Korhonen, PhD.
Coastal Tundrabridge Advisory
PO Box 418259
Quillwater, Alaska 99642
Direct: +1-907-555-0143
Email: mkorhonen@tundrabridgeadvisory.example
Website: www.coastaltundrabridgeadvisory.example

```html
<!DOCTYPE html>
<html lang="en">
<head>
<meta charset="utf-8">
<title>Coastal Tundrabridge Advisory – Business Card</title>
<link href="https://fonts.googleapis.com/css2?family=Roboto:wght@300;400;500;700&display=swap" rel="stylesheet">
<style>
  :root {
    --page-bg: #2b2b2d;
    --card-navy: #111923;
    --card-navy-deep: #0d141d;
    --ink-white: #ffffff;
    --ink-soft: #d8dde4;
    --band-white: #ffffff;
    --band-ink: #111923;
    --divider: #7f8894;
    --emboss-blue: #24366e;
  }
  * { box-sizing: border-box; margin: 0; padding: 0; }
  html, body {
    width: 1200px; height: 780px; overflow: hidden;
    background: var(--page-bg);
    font-family: "Roboto", Arial, sans-serif;
  }
  .canvas {
    width: 1200px; height: 780px;
    display: flex; align-items: center; justify-content: center; gap: 34px;
  }
  .card {
    position: relative;
    width: 555px; height: 317px;
    background: var(--card-navy);
    border-radius: 3px;
    overflow: hidden;
    box-shadow: 0 12px 30px rgba(0,0,0,.45);
  }

  /* Front */
  .front-brand {
    position: absolute; left: 32px; top: 0; bottom: 48px; width: 200px;
    display: flex; align-items: center; gap: 12px;
  }
  .brand-square {
    width: 14px; height: 14px; flex: none;
    background: var(--ink-white);
  }
  .brand-name {
    color: var(--ink-white);
    font-weight: 500; font-size: 18px; line-height: 1.3;
    letter-spacing: 2px; text-transform: uppercase;
  }
  .front-divider {
    position: absolute; left: 248px; top: 58px; height: 150px; width: 1px;
    background: linear-gradient(var(--divider), rgba(127,136,148,.25));
  }
  .holder {
    position: absolute; left: 268px; top: 46px; right: 18px;
    color: var(--ink-white);
  }
  .holder-name { font-size: 27px; line-height: 1.1; letter-spacing: .2px; }
  .holder-name .first { font-weight: 700; }
  .holder-name .last { font-weight: 300; }
  .holder-title { font-size: 16px; font-weight: 500; margin-top: 2px; }
  .contact-list { list-style: none; margin-top: 22px; }
  .contact-list li {
    display: flex; align-items: center; gap: 7px;
    font-size: 11.4px; color: var(--ink-soft); line-height: 1; margin-bottom: 7px;
  }
  .contact-list svg { width: 13px; height: 13px; flex: none; }
  .address-band {
    position: absolute; left: 0; right: 0; bottom: 22px; height: 34px;
    background: var(--band-white);
    display: flex; align-items: center; padding-left: 148px;
    color: var(--band-ink); font-size: 15px; font-weight: 500; letter-spacing: .2px;
  }

  /* Back */
  .card.back { background: linear-gradient(160deg, var(--card-navy) 0%, var(--card-navy-deep) 100%); }
  .back-brand {
    position: absolute; left: 0; right: 0; top: 62px;
    display: flex; align-items: center; justify-content: center; gap: 16px;
  }
  .back-brand .brand-square { width: 22px; height: 22px; background: var(--emboss-blue); }
  .back-brand .brand-name {
    color: var(--emboss-blue); font-size: 30px; font-weight: 700;
    letter-spacing: 4px; line-height: 1.2;
  }
  .services {
    position: absolute; left: 0; right: 0; bottom: 38px;
    text-align: center; color: var(--ink-white);
  }
  .services-heading { font-size: 13.5px; font-weight: 700; letter-spacing: .3px; }
  .services-text { font-size: 12.4px; font-weight: 400; margin-top: 5px; padding: 0 24px; }
</style>
</head>
<body>
<main class="canvas">

  <section class="card front" aria-label="Business card front">
    <div class="front-brand">
      <span class="brand-square"></span>
      <span class="brand-name">Coastal<br>Tundrabridge<br>Advisory</span>
    </div>
    <div class="front-divider"></div>
    <div class="holder">
      <p class="holder-name"><span class="first">Matthias</span> <span class="last">Korhonen</span></p>
      <p class="holder-title">PhD</p>
      <ul class="contact-list">
        <li>
          <svg viewBox="0 0 16 16" aria-hidden="true"><circle cx="8" cy="8" r="7.5" fill="#fff"/><path d="M5.2 4.3l1.4-.3.8 2-1 .7c.5 1.1 1.3 1.9 2.4 2.4l.7-1 2 .8-.3 1.4c-3.3.2-6.2-2.7-6-6z" fill="#111923"/></svg>
          +1-907-555-0143
        </li>
        <li>
          <svg viewBox="0 0 16 16" aria-hidden="true"><rect x="1" y="3" width="14" height="10" rx="1.5" fill="#fff"/><path d="M2 4.2l6 4.6 6-4.6" fill="none" stroke="#111923" stroke-width="1.2"/></svg>
          mkorhonen@tundrabridgeadvisory.example
        </li>
        <li>
          <svg viewBox="0 0 16 16" aria-hidden="true"><circle cx="8" cy="8" r="7.5" fill="#fff"/><g fill="none" stroke="#111923" stroke-width="1"><circle cx="8" cy="8" r="5"/><ellipse cx="8" cy="8" rx="2.2" ry="5"/><path d="M3 8h10"/></g></svg>
          www.coastaltundrabridgeadvisory.example
        </li>
      </ul>
    </div>
    <div class="address-band">PO Box 418259 Quillwater, Alaska 99642</div>
  </section>

  <section class="card back" aria-label="Business card back">
    <div class="back-brand">
      <span class="brand-square"></span>
      <span class="brand-name">Coastal<br>Tundrabridge<br>Advisory</span>
    </div>
    <div class="services">
      <p class="services-heading">OUR SERVICES</p>
      <p class="services-text">We provide specialized permafrost services to the mining, transportation, and oil &amp; gas industries</p>
    </div>
  </section>

</main>
</body>
</html>
```